Local Flower Farm Needs Business Card Design

I need business cards designed for a flower farm based in Eudora, Kansas.
Business Info:
We are a local cut flower farm located in Eudora, Kansas, founded by Corinne Haldwick. What started as a passion for agriculture and search for more joy in daily life has blossomed into a small business dedicated to providing the community with beautiful, fresh, and sustainable flowers. We specialize in local, seasonal blooms, ensuring that every petal reflects the care and dedication we pour into our craft. Our mission is to deliver the highest quality flowers directly to our customers through local farmers markets and to florists who share our commitment to sustainability. Join us in celebrating the beauty of nature, one bloom at a time!
Contact Details:
Corinne Haldwick
Owner
Phone 913-555-0147
Facebook: Rosalind Thorpe Gardens
Instagram: @RosalindThorpeGardens
Website: RosalindThorpeGardens.example
Target Market(s)
Wholesale to Florists and Direct to Consumer via Farmers Market
Industry/Entity Type
Florist, Farm
Contact Information for Business Card
Name, Contact Info, Logo
Look and feel
Each slider illustrates characteristics of the customer's brand and the style your logo design should communicate.

```html
<!DOCTYPE html>
<html lang="en">
<head>
<meta charset="utf-8">
<title>Rosalind Thorpe Gardens – Business Card</title>
<link rel="stylesheet" href="https://fonts.googleapis.com/css2?family=Montserrat:wght@400;500;600;800&display=swap">
<style>
  :root {
    --ink: #0b2a30;
    --teal-deep: #0a2228;
    --teal-mid: #124651;
    --cyan: #5cc6e4;
    --paper: #ffffff;
    --stage: #e9e6e1;
  }
  * { box-sizing: border-box; margin: 0; padding: 0; }
  html, body { width: 1200px; height: 931px; overflow: hidden; }
  body {
    background: var(--stage);
    font-family: "Montserrat", sans-serif;
    color: var(--ink);
    position: relative;
  }
  .card {
    position: absolute;
    width: 620px;
    height: 354px;
    border-radius: 22px;
    overflow: hidden;
    box-shadow: 0 10px 24px rgba(0,0,0,0.18);
  }
  /* Back */
  .card-back { left: 40px; top: 90px; background: var(--teal-deep); }
  .monogram-pattern {
    position: absolute; inset: 0;
    background: linear-gradient(115deg, var(--cyan) 0%, #2f8ea6 18%, var(--teal-mid) 40%, var(--teal-deep) 62%, #081c21 100%);
  }
  .back-mark {
    position: absolute; left: 330px; top: 150px;
    width: 200px;
    color: var(--paper);
    font-weight: 600; font-size: 17px; line-height: 1.25;
    text-align: center;
  }
  /* Front */
  .card-front { left: 540px; top: 470px; background: var(--paper); }
  .brand-seal {
    position: absolute; right: 34px; top: 22px;
    width: 132px; height: 132px;
    border: 1.5px solid var(--ink); border-radius: 50%;
    display: flex; align-items: center; justify-content: center;
    text-align: center;
    font-weight: 600; font-size: 14px; line-height: 1.25;
    color: var(--ink);
  }
  .person-name {
    position: absolute; left: 40px; top: 186px;
    font-weight: 800; font-size: 30px; letter-spacing: -0.3px;
  }
  .rule-long { position: absolute; left: 40px; right: 34px; top: 226px; height: 1.5px; background: var(--ink); }
  .person-role { position: absolute; left: 40px; top: 232px; font-size: 15px; font-weight: 400; }
  .rule-short { position: absolute; left: 40px; width: 200px; top: 256px; height: 1.5px; background: var(--ink); }
  .contact-list {
    position: absolute; left: 40px; top: 266px;
    list-style: none;
    font-size: 14px; line-height: 20px;
  }
  .contact-list li { display: flex; align-items: center; gap: 10px; }
  .contact-list svg { width: 13px; height: 13px; flex: none; }
  .address {
    position: absolute; right: 34px; top: 238px;
    text-align: right; font-size: 13.5px; line-height: 1.35;
  }
</style>
</head>
<body>

<section class="card card-back" aria-label="Card back">
  <div class="monogram-pattern" role="img" aria-label="Repeating floral monogram pattern fading from light cyan to deep teal"></div>
  <div class="back-mark">Rosalind Thorpe Gardens</div>
</section>

<section class="card card-front" aria-label="Card front">
  <div class="brand-seal">Rosalind<br>Thorpe<br>Gardens</div>

  <h1 class="person-name">Corinne Haldwick</h1>
  <div class="rule-long"></div>
  <p class="person-role">Owner</p>
  <div class="rule-short"></div>

  <ul class="contact-list">
    <li>
      <svg viewBox="0 0 16 16" aria-hidden="true"><path fill="var(--ink)" d="M3.5 1.5l2.6 2.6-1.4 1.8c.9 2 2.4 3.5 4.4 4.4l1.8-1.4 2.6 2.6-1.6 2.2C6.7 13.4 2.6 9.3 1.3 3.1z"/></svg>
      913-555-0147
    </li>
    <li>
      <svg viewBox="0 0 16 16" aria-hidden="true"><circle cx="8" cy="8" r="7" fill="var(--ink)"/></svg>
      Rosalind Thorpe Gardens
    </li>
    <li>
      <svg viewBox="0 0 16 16" aria-hidden="true"><circle cx="8" cy="8" r="7" fill="var(--ink)"/></svg>
      @RosalindThorpeGardens
    </li>
    <li>
      <svg viewBox="0 0 16 16" aria-hidden="true"><circle cx="8" cy="8" r="6.3" fill="none" stroke="var(--ink)" stroke-width="1.4"/><path d="M1.7 8h12.6M8 1.7c-3 3.5-3 9.1 0 12.6M8 1.7c3 3.5 3 9.1 0 12.6" fill="none" stroke="var(--ink)" stroke-width="1.1"/></svg>
      www.RosalindThorpeGardens.example
    </li>
  </ul>

  <address class="address" style="font-style:normal">418 Meadowlark Rd, #12<br>Eudora, KS 66025</address>
</section>

</body>
</html>
```